Card Design for my dog training business Brightpaw Obedience

Need a business card design for my dog training business with my new logo. Want the card to come off professional yet fun. Want it to be very eye catchy as well. I normally have these at vet clinics, pet stores, and groomers. so need it to look better than my competitors.
Target Market(s)
dog owners
Industry/Entity Type
Dog Training
Contact Information for Business Card
needs logo, my name and info
Font styles to use
Serif
Colors
0255a3
ffffff
ec1f27
000000
333333
fbfbfb
Requirements
Must have
- Brightpaw Obedience
- Felix Orland
- 415 903 2276
- info@brightpawobedience.example
- www.brightpawobedience.example

```html
<!DOCTYPE html>
<html lang="en">
<head>
<meta charset="utf-8">
<title>Brightpaw Obedience – Business Card</title>
<link rel="stylesheet" href="https://fonts.googleapis.com/css2?family=Lato:wght@400&family=Tinos:wght@400&display=swap">
<style>
  :root {
    --brand-blue: #0255a3;
    --card-white: #ffffff;
    --ink: #000000;
    --ink-soft: #333333;
    --stage: #e9e9e9;
    --divider: #c9c9c9;
    --pattern-blue: #1a63ab;
  }
  * { box-sizing: border-box; margin: 0; padding: 0; }
  html, body {
    width: 1200px; height: 782px; overflow: hidden;
    background: var(--stage);
  }
  .stage {
    position: relative; width: 1200px; height: 782px;
    display: flex; align-items: center; justify-content: center; gap: 50px;
  }
  .card {
    position: relative; width: 540px; height: 309px;
    box-shadow: 0 6px 18px rgba(0,0,0,0.18);
    overflow: hidden;
  }
  /* front */
  .card--front {
    background: var(--card-white);
    border-bottom: 8px solid var(--brand-blue);
  }
  .brand-lockup {
    position: absolute; left: 24px; top: 0; width: 190px; height: 301px;
    display: flex; flex-direction: column; align-items: center; justify-content: center; gap: 14px;
  }
  .brand-lockup__mark {
    width: 28px; height: 28px; background: var(--ink);
  }
  .brand-name {
    font-family: "Tinos", "Times New Roman", serif;
    font-weight: 400; font-size: 24px; line-height: 1.15; color: var(--ink);
    text-align: center; letter-spacing: 0.04em;
  }
  .divider {
    position: absolute; left: 232px; top: 70px; width: 1px; height: 160px;
    background: linear-gradient(to bottom, transparent, var(--divider) 20%, var(--divider) 80%, transparent);
  }
  .contact-block {
    position: absolute; left: 256px; right: 18px; top: 96px;
  }
  .person-name {
    font-family: "Tinos", "Times New Roman", serif;
    font-weight: 400; font-size: 20px; letter-spacing: 0.04em; color: var(--ink-soft);
    text-transform: uppercase; margin-bottom: 24px;
  }
  .contact-list { list-style: none; }
  .contact-list li {
    display: flex; align-items: center; gap: 7px;
    font-family: "Lato", Arial, sans-serif; font-size: 13px; line-height: 21px;
    color: var(--ink); white-space: nowrap;
  }
  .contact-list svg { width: 11px; height: 11px; flex: none; fill: var(--ink-soft); }
  /* back */
  .card--back { background: var(--brand-blue); }
  .back-pattern {
    position: absolute; inset: 0;
    background: radial-gradient(circle at 50% 40%, var(--pattern-blue), var(--brand-blue) 75%);
  }
  .back-name {
    position: absolute; right: 36px; bottom: 42px;
    font-family: "Tinos", "Times New Roman", serif;
    font-weight: 400; font-size: 17px; line-height: 1.2; color: var(--card-white);
    text-align: center; letter-spacing: 0.04em;
  }
</style>
</head>
<body>
<main class="stage">
  <section class="card card--front" aria-label="Business card front">
    <div class="brand-lockup">
      <span class="brand-lockup__mark"></span>
      <p class="brand-name">Brightpaw<br>Obedience</p>
    </div>
    <div class="divider"></div>
    <div class="contact-block">
      <h1 class="person-name">Felix Orland</h1>
      <ul class="contact-list">
        <li>
          <svg viewBox="0 0 24 24"><path d="M6.6 10.8a15.1 15.1 0 0 0 6.6 6.6l2.2-2.2a1 1 0 0 1 1-.25 11.4 11.4 0 0 0 3.6.57 1 1 0 0 1 1 1V20a1 1 0 0 1-1 1A17 17 0 0 1 3 4a1 1 0 0 1 1-1h3.5a1 1 0 0 1 1 1c0 1.25.2 2.45.57 3.57a1 1 0 0 1-.25 1z"/></svg>
          415 903 2276
        </li>
        <li>
          <svg viewBox="0 0 24 24"><path d="M2 5h20v14H2zm2 2v.5l8 5 8-5V7l-8 5z"/></svg>
          info@brightpawobedience.example
        </li>
        <li>
          <svg viewBox="0 0 24 24"><circle cx="12" cy="12" r="10"/></svg>
          www.brightpawobedience.example
        </li>
      </ul>
    </div>
  </section>

  <section class="card card--back" aria-label="Business card back">
    <div class="back-pattern" role="img" aria-label="Faint repeating brand pattern in tonal blue"></div>
    <p class="back-name">Brightpaw<br>Obedience</p>
  </section>
</main>
</body>
</html>
```